Lawn Sign Design – Brisqel

We need a clean, eye-catching 18" x 24" lawn sign for Brisqel that effectively communicates our core message while maintaining strong brand consistency.

Key Elements to Include:
Tagline (Main Focus): Upgrade Your Roof Without Replacing It
Website: www.trybrisqel.com
Phone Number: (888) BRISQEL-GO
TWQB License Number: 4480512
Brisqel Logo & Branding: Ensure the logo, corporate colors, and custom font are used consistently to align with our existing branding.

Design Guidelines:
Simple & High-Impact: The tagline should be the most prominent element on the sign, drawing immediate attention.
Easy Readability: Use a bold, clean design with high contrast for quick readability from a distance.
Balanced Layout: Place supporting details (website, phone number, and TWQB number) in a visually clear but secondary position to the tagline.
Professional & Modern: The sign should reflect credibility and innovation in the roofing industry.

Deliverables:
High-resolution print-ready files (CMYK)
A digital proof for review before finalizing
The final design should make a strong impression with minimal text, ensuring that anyone passing by can instantly grasp what we offer.

I am including our custom font. To get an hexagon in our name, simply type the $ after the 'O" Please use this font for anything you type.

```html
<!DOCTYPE html>
<html lang="en">
<head>
<meta charset="utf-8">
<title>Brisqel Lawn Sign</title>
<link rel="stylesheet" href="https://fonts.googleapis.com/css2?family=Nunito:wght@700;800;900&display=swap">
<style>
  :root {
    --stage: #5e5e5e;
    --paper: #ffffff;
    --paper-shade: #eceef1;
    --brand-blue: #1a4f9c;
    --accent-blue: #1f5fc8;
    --line-blue: #2856b8;
    --panel-black: #111111;
    --sky-top: #0a78d0;
    --sky-bottom: #9cc8ec;
    --ink-white: #ffffff;
    --ink-black: #0d0d0d;
  }
  html, body {
    margin: 0;
    padding: 0;
    width: 1200px;
    height: 2302px;
    overflow: hidden;
    background: var(--stage);
  }
  .sign {
    position: absolute;
    left: 60px;
    top: 432px;
    width: 1080px;
    height: 1438px;
    box-shadow: 8px 14px 30px rgba(0, 0, 0, 0.45);
  }
  .sign svg {
    display: block;
    width: 100%;
    height: 100%;
    font-family: "Nunito", Arial, sans-serif;
  }
  .headline { font-weight: 900; text-anchor: middle; }
  .headline-white { fill: var(--ink-white); }
  .headline-blue { fill: var(--accent-blue); }
  .kicker { font-weight: 800; fill: var(--ink-white); text-anchor: middle; letter-spacing: 5px; }
  .brand-name { font-weight: 800; fill: var(--ink-white); text-anchor: middle; letter-spacing: 2px; }
  .contact { font-weight: 800; fill: var(--ink-white); }
  .license-label { font-weight: 800; fill: var(--ink-black); text-anchor: middle; }
  .license-number { font-weight: 800; fill: var(--ink-white); text-anchor: middle; letter-spacing: 3px; }
</style>
</head>
<body>
  <main class="sign">
    <svg viewBox="0 0 892 1188" xmlns="http://www.w3.org/2000/svg" aria-label="Brisqel lawn sign: Upgrade your roof without replacing it">
      <defs>
        <linearGradient id="paperGradient" x1="0" y1="0" x2="1" y2="1">
          <stop offset="0" stop-color="var(--paper-shade)"/>
          <stop offset="0.5" stop-color="var(--paper)"/>
          <stop offset="1" stop-color="var(--paper-shade)"/>
        </linearGradient>
        <linearGradient id="photoGradient" x1="0" y1="0" x2="0" y2="1">
          <stop offset="0" stop-color="var(--sky-top)"/>
          <stop offset="0.45" stop-color="var(--sky-bottom)"/>
          <stop offset="0.7" stop-color="#d9dde2"/>
          <stop offset="1" stop-color="#5d7a45"/>
        </linearGradient>
        <linearGradient id="kickerBand" x1="0" y1="0" x2="1" y2="0">
          <stop offset="0" stop-color="#1a3f86" stop-opacity="0"/>
          <stop offset="0.5" stop-color="#1a3f86"/>
          <stop offset="1" stop-color="#1a3f86" stop-opacity="0"/>
        </linearGradient>
      </defs>

      <!-- backdrop bands -->
      <rect class="backdrop-light" x="0" y="0" width="892" height="473" fill="url(#paperGradient)"/>
      <rect class="backdrop-blue" x="0" y="473" width="892" height="715" fill="var(--brand-blue)"/>

      <!-- house photo frame -->
      <polygon class="house-photo" role="img" aria-label="Photo of a white two-storey house with grey shingle roof, porch and garden under a blue sky"
               points="78,283 446,70 815,70 815,713 446,918 78,713" fill="url(#photoGradient)"/>

      <!-- headline panel -->
      <rect class="headline-panel" x="446" y="70" width="369" height="420" fill="var(--panel-black)"/>

      <!-- accent lines -->
      <line class="accent-line" x1="103" y1="251" x2="446" y2="55" stroke="var(--line-blue)" stroke-width="6"/>
      <line class="frame-line" x1="55" y1="713" x2="399" y2="910" stroke="var(--ink-white)" stroke-width="6"/>
      <line class="frame-line" x1="496" y1="910" x2="839" y2="713" stroke="var(--ink-white)" stroke-width="6"/>

      <!-- tagline -->
      <text class="headline headline-white" x="634" y="185" font-size="64" textLength="314" lengthAdjust="spacingAndGlyphs">UPGRADE</text>
      <text class="headline headline-blue" x="634" y="236" font-size="56" textLength="314" lengthAdjust="spacingAndGlyphs">YOUR ROOF</text>
      <rect class="kicker-band" x="504" y="253" width="260" height="24" fill="url(#kickerBand)"/>
      <text class="kicker" x="634" y="272" font-size="20">WITHOUT</text>
      <text class="headline headline-blue" x="634" y="323" font-size="40" textLength="274" lengthAdjust="spacingAndGlyphs">REPLACING IT</text>

      <!-- brand -->
      <circle class="brand-mark" cx="179" cy="1005" r="36" fill="none" stroke="var(--ink-white)" stroke-width="7"/>
      <text class="brand-name" x="179" y="1113" font-size="46" textLength="214" lengthAdjust="spacingAndGlyphs">BRISQEL</text>

      <!-- phone -->
      <circle class="phone-badge" cx="362" cy="980" r="27" fill="var(--panel-black)"/>
      <path class="phone-icon" d="M352 966 c3-2 6 0 7 3 l2 5 c1 2 0 4-2 5 l-2 1 c1 4 5 9 9 10 l1-2 c1-2 3-3 5-2 l5 2 c3 1 4 4 3 7 c-2 4-6 5-10 4 c-10-3-18-11-21-21 c-1-5 0-9 3-12 z" fill="var(--ink-white)"/>
      <text class="contact contact-phone" x="402" y="994" font-size="46" textLength="413" lengthAdjust="spacingAndGlyphs">(888) BRISQEL-GO</text>

      <!-- website -->
      <text class="contact contact-web" x="336" y="1047" font-size="38" textLength="481" lengthAdjust="spacing">www.trybrisqel.com</text>

      <!-- license -->
      <rect class="license-label-box" x="336" y="1071" width="320" height="44" rx="6" fill="var(--paper)"/>
      <text class="license-label" x="496" y="1102" font-size="25">TWQB License Number</text>
      <rect class="license-number-box" x="660" y="1071" width="158" height="44" rx="6" fill="var(--panel-black)"/>
      <text class="license-number" x="739" y="1102" font-size="25">4480512</text>
    </svg>
  </main>
</body>
</html>
```